Car Signage & Personal Branding - Email & Letterhead

I require a ¼ wrap on 2014 Korvana Delmire Ridgeback - Colour Glacier Blue.
Covering the follow...
- rear panel and small window
- passenger door & ½ of the passenger window - top left to bottom right, can blend into drivers door. (more than what is showed on the image)

This design will then be required as Email & letter header and branding for advertising.

I'm a Gold Coast real estate agent and want something thats clear, professional, people say WOW and isn't like all other boring vehicle wraps.

To feature my image and get across that I'm honest reliable, ethical, tenacious, hard working, talented.

I do like these font advertising styles (see Word Doc) )but I'm not the professional and want something from you.

I like light sky/ocean blue but may not work against a light blue car. I like the way 2 photos are blended together, wonder if that can be done professionally with the gold coast & my photo.

Brindle colours are 100% black, cyan & white. Must have their logo on it.

Have included some font advertising styles that you may think would look good, obviously only use these if you think they're suitable.
Updates

Residential, development & land sales on the gold coast Added Thursday, June 11, 2015

Design can go over small rear window and the black plastic on the passenger window but not the glass. There must be a gap for the passenger door handle. The rear of the car, it can go over the glass & it must have all my phone number. Added Friday, June 12, 2015

Target Market(s)

Clients and other drivers

Industry/Entity Type

Real Estate Agent

Requirements
Must have
• My photo
• Company logo
• 040 555 3186
• lucyt@brindleco.com.au
• www.lucytambor.com
• Wave image
• Will cover the complete rear hatch of the car.
• can cover back rear ¼ glass window and then come down through passenger window on the angle to the bottom corner
Nice to have
• Image of Gold Coast or waves
• What you would imagine on a multi-million dollar real estate agents car
Should not have
• Can not cover drivers window
• Can not cover any door handles

```html
<!DOCTYPE html>
<html lang="en">
<head>
<meta charset="utf-8">
<title>Brindle – Lucy Tambor Letterhead</title>
<link href="https://fonts.googleapis.com/css2?family=Open+Sans:wght@400;600&display=swap" rel="stylesheet">
<style>
  :root {
    --cyan: #00aeef;
    --header-dark: #231f20;
    --paper: #ffffff;
    --ink: #231f20;
    --rule: #e3e3e3;
    --watermark: #eef7fc;
  }
  * { margin: 0; padding: 0; box-sizing: border-box; }
  html, body { width: 928px; height: 1200px; overflow: hidden; background: var(--paper); }
  .letterhead {
    position: relative;
    width: 928px;
    height: 1200px;
    background: var(--paper);
    font-family: "Open Sans", Arial, sans-serif;
    overflow: hidden;
  }
  .top-stripe {
    position: absolute; left: 0; top: 0;
    width: 100%; height: 12px;
    background: var(--cyan);
  }
  .header-band {
    position: absolute; left: 0; top: 12px;
    width: 705px; height: 138px;
    background: var(--header-dark);
  }
  .brand {
    position: absolute; left: 34px; top: 44px;
    display: flex; align-items: center; gap: 12px;
  }
  .brand-dot {
    width: 46px; height: 46px; border-radius: 50%;
    background: var(--cyan);
  }
  .brand-name {
    color: var(--paper);
    font-weight: 600;
    font-size: 64px;
    line-height: 1;
    letter-spacing: -1px;
  }
  .agent-photo {
    position: absolute; left: 520px; top: 12px;
    width: 185px; height: 138px;
    background: linear-gradient(100deg, #2a2522 0%, #8a6d4e 30%, #d9b894 55%, #c9a070 72%, #5c5a3a 100%);
  }
  .contact-panel {
    position: absolute; left: 705px; top: 12px;
    width: 223px; height: 138px;
    border-bottom: 1px solid var(--rule);
  }
  .contact-list {
    list-style: none;
    position: absolute; left: 12px; top: 50px;
  }
  .contact-list li {
    display: flex; align-items: center; gap: 7px;
    height: 18.5px;
    font-size: 13.5px;
    color: var(--ink);
  }
  .contact-list svg { width: 14px; height: 14px; flex: none; }
  .contact-rule {
    position: absolute; left: 0; top: 105px;
    width: 100%; height: 1px; background: var(--rule);
  }
  .watermark {
    position: absolute; left: 0; top: 0;
    width: 928px; height: 1200px;
    pointer-events: none;
  }
</style>
</head>
<body>
<div class="letterhead">
  <svg class="watermark" viewBox="0 0 928 1200" aria-hidden="true">
    <circle cx="612" cy="930" r="300" fill="none" stroke="var(--watermark)" stroke-width="42"/>
  </svg>

  <div class="top-stripe"></div>

  <header>
    <div class="header-band"></div>
    <div class="brand">
      <span class="brand-dot"></span>
      <span class="brand-name">Brindle</span>
    </div>
    <div class="agent-photo" role="img" aria-label="Portrait photograph of the agent, Lucy Tambor"></div>

    <div class="contact-panel">
      <ul class="contact-list">
        <li>
          <svg viewBox="0 0 14 14"><circle cx="7" cy="7" r="6.3" fill="none" stroke="var(--cyan)" stroke-width="1.1"/><path d="M4.6 3.8l1.3-.3.7 1.7-.8.6c.4.9 1 1.5 1.9 1.9l.6-.8 1.7.7-.3 1.3c-2.7.2-5.3-2.4-5.1-5.1z" fill="var(--cyan)"/></svg>
          <span>040 555 3186</span>
        </li>
        <li>
          <svg viewBox="0 0 14 14"><circle cx="7" cy="7" r="6.8" fill="var(--cyan)"/><rect x="3.5" y="4.6" width="7" height="4.8" fill="#fff"/><path d="M3.5 4.6L7 7.4l3.5-2.8" fill="none" stroke="var(--cyan)" stroke-width=".9"/></svg>
          <span>lucyt@brindleco.com.au</span>
        </li>
        <li>
          <svg viewBox="0 0 14 14"><circle cx="7" cy="7" r="6.3" fill="none" stroke="var(--cyan)" stroke-width="1.2"/><ellipse cx="7" cy="7" rx="2.6" ry="6.3" fill="none" stroke="var(--cyan)" stroke-width="1"/><path d="M.8 7h12.4M1.8 4h10.4M1.8 10h10.4" stroke="var(--cyan)" stroke-width="1"/></svg>
          <span>www.lucytambor.com</span>
        </li>
      </ul>
      <div class="contact-rule"></div>
    </div>
  </header>
</div>
</body>
</html>
```